Brookvale Estates LLC stationary for a real estate property management company.

Create stationary (letterhead, envelopes, business cards) using Brookvale Estates LLC logo as primary creative element. Stationary design needs to be horizontal, leaving as much space as possible for correspondence copy. See attached Creative Brief and past stationary files for details.

Target Market(s)

Prospective apartment residents and current residents, vendors, and government agencies.

Industry/Entity Type

Property Management

Contact Information for Business Card

Business card employee title: Property Manager. Should include address, phone, fax, email, website, slogan, and Brookvale Estates logo.

Font styles to use
Sans Serif

Colors
0592cd
000000

Requirements
Must have
• Tone should be conservative, institutional, business (i.e. banking, finance, real estate). Must include: address, phone, fax, website, and slogan (see attached Creative Brief). Should be a horizontal design, leaving as much room as possible for letter correspondence copy.
Nice to have
• Please use an Arial or Helvetica style font.
Should not have
• Letterhead layout should leave as much room as possible for copy.

```html
<!DOCTYPE html>
<html lang="en">
<head>
<meta charset="utf-8">
<title>Brookvale Estates LLC – Business Card</title>
<link rel="stylesheet" href="https://fonts.googleapis.com/css2?family=Arimo:wght@400;700&display=swap">
<style>
  :root {
    --brand-blue: #0a6fb0;
    --brand-cyan: #1ab9ec;
    --brand-deep: #0763a1;
    --ink: #3a3a3a;
    --ink-dark: #444;
    --paper: #f7f7f7;
    --stage: #e6e6e6;
    --white: #ffffff;
  }
  * { margin: 0; padding: 0; box-sizing: border-box; }
  html, body { width: 1200px; height: 960px; overflow: hidden; }
  body {
    background: var(--stage);
    font-family: "Arimo", Arial, sans-serif;
    position: relative;
  }
  .card { position: absolute; width: 600px; height: 340px; overflow: hidden; }

  /* Front */
  .card-front { left: 302px; top: 130px; background: var(--paper); }
  .front-wordmark {
    position: absolute; right: 30px; top: 64px; text-align: right;
    color: var(--brand-blue); font-weight: 700; line-height: 1;
  }
  .front-wordmark .line-main { font-size: 33px; letter-spacing: 0.5px; }
  .front-wordmark .line-sub { font-size: 14px; letter-spacing: 3px; margin-top: 4px; }

  .name-marker { position: absolute; left: 0; top: 191px; width: 8px; height: 36px; background: var(--brand-blue); }
  .person-name { position: absolute; left: 28px; top: 189px; font-size: 20px; font-weight: 700; color: var(--brand-blue); }
  .person-title { position: absolute; left: 28px; top: 214px; font-size: 15px; color: var(--ink); }
  .divider { position: absolute; left: 28px; right: 30px; top: 240px; height: 1px; background: #222; }

  .contact-list { position: absolute; left: 28px; top: 252px; list-style: none; font-size: 14px; color: var(--ink); }
  .contact-list li { display: flex; align-items: center; height: 19px; }
  .contact-list svg { width: 13px; height: 13px; margin-right: 9px; fill: var(--brand-blue); }

  .address-block { position: absolute; right: 30px; top: 252px; text-align: right; font-size: 14px; line-height: 19px; color: var(--ink); }
  .address-block .web { letter-spacing: 0.6px; }

  .footer-band { position: absolute; left: 0; bottom: 0; width: 600px; height: 24px; }
  .slogan {
    position: absolute; right: 18px; bottom: 3px; font-size: 14px; color: var(--white);
  }

  /* Back */
  .card-back {
    left: 299px; top: 488px; height: 342px;
    background: linear-gradient(135deg, var(--brand-cyan) 0%, var(--brand-blue) 45%, var(--brand-deep) 100%);
  }
  .back-wordmark {
    position: absolute; left: 0; right: 0; top: 146px; text-align: center;
    color: var(--white); font-weight: 700; line-height: 1;
  }
  .back-wordmark .line-main { font-size: 56px; letter-spacing: 1px; }
  .back-wordmark .line-sub { font-size: 20px; letter-spacing: 5px; margin-top: 8px; }
</style>
</head>
<body>

<section class="card card-front" aria-label="Business card front">
  <div class="front-wordmark">
    <div class="line-main">BROOKVALE</div>
    <div class="line-sub">ESTATES LLC</div>
  </div>

  <div class="name-marker"></div>
  <h1 class="person-name">DANIEL REEVES</h1>
  <p class="person-title">Property Manager</p>
  <div class="divider"></div>

  <ul class="contact-list">
    <li>
      <svg viewBox="0 0 24 24" aria-hidden="true"><path d="M6.6 10.8a15.1 15.1 0 0 0 6.6 6.6l2.2-2.2a1 1 0 0 1 1-.25 11.4 11.4 0 0 0 3.6.6 1 1 0 0 1 1 1V20a1 1 0 0 1-1 1A17 17 0 0 1 3 4a1 1 0 0 1 1-1h3.5a1 1 0 0 1 1 1c0 1.25.2 2.45.6 3.6a1 1 0 0 1-.25 1z"/></svg>
      555-214-7730
    </li>
    <li>
      <svg viewBox="0 0 24 24" aria-hidden="true"><path d="M6 2h12v6H6z"/><path d="M3 9h18a1 1 0 0 1 1 1v7h-4v5H6v-5H2v-7a1 1 0 0 1 1-1zm5 7v4h8v-4z"/></svg>
      555-214-7731
    </li>
    <li>
      <svg viewBox="0 0 24 24" aria-hidden="true"><path d="M2 5h20v14H2zm2 2v.4l8 5.2 8-5.2V7zm0 2.8V17h16V9.8l-8 5.2z"/></svg>
      daniel@brookvaleestates.us
    </li>
  </ul>

  <address class="address-block" style="font-style:normal">
    2750 Harbor Ridge Drive #B210<br>
    Lakemont, CA 90871<br>
    <span class="web">www.brookvaleestates.us</span>
  </address>

  <svg class="footer-band" viewBox="0 0 600 24" preserveAspectRatio="none" aria-hidden="true">
    <path d="M0 0 H332 Q338 0 342 -2 L346 4 Q340 7 332 7 H0 Z" fill="#444"/>
    <path d="M0 7 H334 Q340 7 346 2 L600 2 V24 H0 Z" fill="#444"/>
    <path d="M0 14 H330 Q342 14 348 5 Q352 0 360 0 H600 V24 H0 Z" fill="#0a6fb0"/>
  </svg>
  <p class="slogan">Multifamily Property Management</p>
</section>

<section class="card card-back" aria-label="Business card back">
  <div class="back-wordmark">
    <div class="line-main">BROOKVALE</div>
    <div class="line-sub">ESTATES LLC</div>
  </div>
</section>

</body>
</html>
```